Business Card Design Project

We have recently completed CraftHive projects for a new logo and wesbite.
We now require new business cards.
We hand out very little printed material to clients as all information is online. When we do hand out something, like a business card, we want it to have real impact and make a statement about the quality and professionalism of our company.
We have an idea of what we want our card to look like but we want a designer to make sure they have impact and look great.
Our requirements are…
Size: 85mm X 55mm - Landscape
Front of card: Logo plus the following contact information.
Dennis Marlow
Operations Manager
Phone +44(0) 1632 xxx xxx
Mobile +44(0) 7700 xxx xxx
Email denmo@korvantix.example
Address 17 Pellick Row, Aberdeen AB12 9QZ
Website www.korvantix.example
How you layout the front of the card is up to you, we would like to see some different ideas. Attached are two versions of our logo that may be used.
Back of card: We would like this to be simple but again have impact. Our current thought is to have the logo or just the large W design from the logo in white against a dark background, perhaps made up from the dark green in the logo.
The logos are attached so you can see the colours in them but the dark ones are..
Dark Blue = C:88, M:55, Y:44, K:28
Dark Green = C:87, M:53, Y:50, K:50
We sometimes also use a bright orange as an accent or highlight colour…
Orange: = C:0, M:39, Y:94, K:0

```html
<!DOCTYPE html>
<html lang="en">
<head>
<meta charset="utf-8">
<title>Korvantix Technologies – Business Cards</title>
<link href="https://fonts.googleapis.com/css2?family=Open+Sans:wght@400;600;700;800&display=swap" rel="stylesheet">
<style>
  :root {
    --backdrop: #e9e7e3;
    --ink-dark: #1f4650;
    --ink-text: #2c3e44;
    --teal-dark: #23434b;
    --teal-mid: #3d6b74;
    --teal-light: #6aa5aa;
    --olive: #7f9560;
    --white: #ffffff;
    --card-shadow: 0 3px 10px rgba(0,0,0,0.25);
  }
  * { margin: 0; padding: 0; box-sizing: border-box; }
  html, body { width: 1200px; height: 800px; overflow: hidden; }
  body {
    background: var(--backdrop);
    font-family: "Open Sans", Arial, sans-serif;
    position: relative;
  }
  .card {
    position: absolute;
    width: 502px;
    height: 325px;
    box-shadow: var(--card-shadow);
    overflow: hidden;
  }
  .card--front { left: 80px; top: 63px; background: var(--white); }
  .card--back-dark { left: 610px; top: 68px; background: var(--teal-dark); }
  .card--back-gradient { left: 86px; top: 408px; background: linear-gradient(135deg, var(--teal-dark) 0%, #4d6b58 50%, var(--olive) 85%); }
  .card--back-light { left: 610px; top: 408px; background: var(--white); }

  /* Front: brand block */
  .brand {
    position: absolute;
    left: 46px;
    top: 36px;
    width: 210px;
    text-align: center;
    color: var(--ink-dark);
    font-weight: 800;
  }
  .brand__dot {
    width: 74px; height: 74px;
    border-radius: 50%;
    background: var(--teal-mid);
    margin: 0 auto 18px;
  }
  .brand__name { font-size: 34px; line-height: 1; letter-spacing: -0.5px; }
  .brand__tagline { font-size: 17px; letter-spacing: 4.5px; margin-top: 6px; }

  /* Front: contact block */
  .contact {
    position: absolute;
    left: 296px;
    top: 64px;
    color: var(--ink-text);
  }
  .contact__name { font-size: 17px; font-weight: 700; color: var(--ink-dark); letter-spacing: 0.3px; }
  .contact__role { font-size: 13px; margin-top: 1px; }
  .contact__list { list-style: none; margin-top: 18px; font-size: 13px; line-height: 19px; }
  .contact__list li { display: flex; align-items: center; gap: 6px; }
  .contact__icon { width: 11px; height: 11px; flex: none; fill: var(--ink-text); }

  /* Front: band */
  .band {
    position: absolute;
    left: 0; top: 234px;
    width: 100%; height: 36px;
  }
  .band__bar-left {
    position: absolute; left: 0; top: 0; width: 348px; height: 100%;
    background: linear-gradient(90deg, var(--teal-dark), var(--teal-light));
  }
  .band__bar-right {
    position: absolute; right: 0; top: 0; width: 46px; height: 100%;
    background: var(--teal-light);
  }
  .band__mark {
    position: absolute; left: 350px; top: 0; width: 106px; height: 100%;
    display: flex; align-items: center; justify-content: center;
    font-size: 14px; font-weight: 800; color: var(--teal-mid);
  }
  .address {
    position: absolute;
    left: 0; top: 288px; width: 100%;
    text-align: center;
    padding-left: 10px;
    font-size: 13px;
    color: var(--ink-text);
  }

  /* Backs */
  .back-mark {
    position: absolute;
    left: 0; top: 58px; width: 100%;
    display: flex; flex-direction: column; align-items: center;
    font-weight: 800;
    font-size: 54px;
    line-height: 1;
    letter-spacing: 1px;
  }
  .back-mark__dot {
    width: 96px; height: 96px; border-radius: 50%;
    margin-bottom: 20px;
  }
  .back-url {
    position: absolute;
    left: 0; top: 266px; width: 100%;
    text-align: center;
    font-size: 15px;
    letter-spacing: 3px;
  }
  .on-dark { color: var(--white); }
  .on-dark .back-mark__dot { background: var(--white); }
  .on-light { color: var(--ink-dark); }
  .on-light .back-mark { color: var(--teal-mid); }
  .on-light .back-mark__dot { background: var(--teal-mid); }
  .card--back-gradient .back-mark { top: 50px; }
  .card--back-gradient .back-url { top: 268px; }
</style>
</head>
<body>

  <section class="card card--front">
    <div class="brand">
      <div class="brand__dot"></div>
      <div class="brand__name">KORVANTIX</div>
      <div class="brand__tagline">TECHNOLOGIES</div>
    </div>

    <div class="contact">
      <div class="contact__name">DENNIS MARLOW</div>
      <div class="contact__role">Operations Manager</div>
      <ul class="contact__list">
        <li>
          <svg class="contact__icon" viewBox="0 0 12 12" aria-hidden="true"><path d="M2.5 0.8 L4.3 0.5 L5.2 3 L4 3.9 Q5 6.3 7.9 7.9 L8.9 6.8 L11.4 7.8 L11.1 9.6 Q10 11.5 8 11 Q2.5 9.2 0.9 3.9 Q0.5 1.8 2.5 0.8Z"/></svg>
          +44(0) 1632 xxx xxx
        </li>
        <li>
          <svg class="contact__icon" viewBox="0 0 12 12" aria-hidden="true"><path d="M3.5 0.5 H8.5 V11.5 H3.5 Z M4.4 1.6 V8.6 H7.6 V1.6 Z M5.6 9.5 H6.4 V10.3 H5.6 Z" fill-rule="evenodd"/></svg>
          +44(0) 7700 xxx xxx
        </li>
        <li>
          <svg class="contact__icon" viewBox="0 0 12 12" aria-hidden="true"><path d="M0.5 2.5 H11.5 V10 H0.5 Z M1.2 3 L6 6.6 L10.8 3 Z" fill-rule="evenodd"/></svg>
          denmo@korvantix.example
        </li>
        <li>
          <svg class="contact__icon" viewBox="0 0 12 12" aria-hidden="true"><circle cx="6" cy="6" r="5" fill="none" stroke="currentColor" stroke-width="1"/><ellipse cx="6" cy="6" rx="2.2" ry="5" fill="none" stroke="#2c3e44" stroke-width="0.9"/><path d="M1 6 H11" stroke="#2c3e44" stroke-width="0.9"/></svg>
          www.korvantix.example
        </li>
      </ul>
    </div>

    <div class="band">
      <div class="band__bar-left"></div>
      <div class="band__mark">KORVANTIX</div>
      <div class="band__bar-right"></div>
    </div>

    <div class="address">17 Pellick Row, Aberdeen AB12 9QZ</div>
  </section>

  <section class="card card--back-dark on-dark">
    <div class="back-mark">
      <div class="back-mark__dot"></div>
      KORVANTIX
    </div>
    <div class="back-url">www.korvantix.example</div>
  </section>

  <section class="card card--back-gradient on-dark">
    <div class="back-mark">
      <div class="back-mark__dot"></div>
      KORVANTIX
    </div>
    <div class="back-url">www.korvantix.example</div>
  </section>

  <section class="card card--back-light on-light">
    <div class="back-mark">
      <div class="back-mark__dot"></div>
      KORVANTIX
    </div>
    <div class="back-url">www.korvantix.example</div>
  </section>

</body>
</html>
```